Coastal Gin Label Design

We are needing a nautical/coastal themed label for our upcoming gin release.

We have saltbush, cucumber, juniper, and quandong being used in this gin.

Name of the Gin; Harbour Moons

The logo attached is the company logo, but doesn't have to be used on the front of the label, ie it can just be the name Fernwhistle somewhere on the front.
Bottle specs attached as well so you can accurately represent the bottle- this bottle is also clear.

Target Market(s)

Women 25- 45

Font styles to use
Serif
Decorative

Colors
d5edf4
86cae7
33a6d7
86cfc6
cfeae6
ffffff
f6faec
ecf7fb
fefeff

Requirements
Must have
• Ocean/Coastal vibe to the label
Nice to have
• Blues,Whites clean and crisp
Should not have
• No generic word art look to it.
A dark mood

```html
<!DOCTYPE html>
<html lang="en">
<head>
<meta charset="utf-8">
<title>Fernwhistle Harbour Moons Gin Label</title>
<link href="https://fonts.googleapis.com/css2?family=Cinzel:wght@500&family=Bowlby+One&family=Josefin+Sans:wght@600&family=Oswald:wght@300&display=swap" rel="stylesheet">
<style>
  :root {
    --page: #ffffff;
    --label: #ffffff;
    --gold: #b8923a;
    --teal: #55bcb8;
    --sea-deep: #14a79b;
    --sea: #3fbcae;
    --sand: #e4d9b8;
    --foam: #f6faf6;
    --white: #ffffff;
  }
  * { margin: 0; padding: 0; box-sizing: border-box; }
  html, body {
    width: 1200px; height: 1193px; overflow: hidden;
    background: var(--page);
  }
  .label {
    position: absolute;
    left: 350px; top: 272px;
    width: 530px; height: 673px;
    background: var(--label);
    box-shadow: 0 2px 10px rgba(0,0,0,0.12);
    overflow: hidden;
  }
  .label__scene {
    position: absolute; inset: 0;
    width: 100%; height: 100%;
  }
  .label__brand {
    position: absolute; top: 60px; left: 0; right: 0;
    text-align: center;
    font-family: "Cinzel", serif; font-weight: 500;
    font-size: 39px; letter-spacing: 0.5px;
    color: var(--gold);
  }
  .label__name {
    position: absolute; top: 152px; left: 0; right: 0;
    text-align: center;
    font-family: "Bowlby One", sans-serif;
    color: var(--teal);
    line-height: 0.98;
  }
  .label__name-line { display: block; font-size: 82px; }
  .label__name-line--second { font-size: 86px; }
  .label__type {
    position: absolute; top: 465px; left: 0; right: 0;
    text-align: center;
    font-family: "Josefin Sans", sans-serif; font-weight: 600;
    font-size: 66px; letter-spacing: 14px; padding-left: 14px;
    color: var(--white);
    text-shadow: 3px 4px 5px rgba(0,60,60,0.45);
  }
  .label__rule {
    position: absolute; top: 578px; left: 139px;
    width: 250px; height: 2px;
    background: var(--white);
  }
  .label__specs {
    position: absolute; top: 588px; left: 0; right: 0;
    text-align: center;
    font-family: "Oswald", sans-serif; font-weight: 300;
    font-size: 24px; color: var(--white);
    word-spacing: 2px;
  }
  .label__specs span + span { margin-left: 24px; }
</style>
</head>
<body>
  <main class="label">
    <svg class="label__scene" viewBox="0 0 530 673" role="img" aria-label="Aerial photograph of turquoise ocean waves washing onto a sandy beach, framing the label from top-left and bottom-right">
      <defs>
        <filter id="soft" x="-20%" y="-20%" width="140%" height="140%">
          <feGaussianBlur stdDeviation="14"/>
        </filter>
        <linearGradient id="shoreTop" x1="0" y1="0" x2="1" y2="1">
          <stop offset="0" stop-color="var(--sea)"/>
          <stop offset="0.35" stop-color="var(--sand)"/>
          <stop offset="0.7" stop-color="var(--foam)"/>
        </linearGradient>
        <linearGradient id="shoreBottom" x1="0" y1="0" x2="1" y2="1">
          <stop offset="0.2" stop-color="var(--foam)"/>
          <stop offset="0.42" stop-color="var(--sand)"/>
          <stop offset="0.62" stop-color="var(--sea)"/>
          <stop offset="1" stop-color="var(--sea-deep)"/>
        </linearGradient>
      </defs>
      <path d="M-20 -20 L345 -20 L240 40 L150 110 L60 150 L-20 170 Z" fill="url(#shoreTop)" filter="url(#soft)"/>
      <path d="M550 290 L550 700 L-20 700 L-20 560 L60 470 L170 410 L290 360 L420 320 Z" fill="url(#shoreBottom)" filter="url(#soft)"/>
    </svg>

    <div class="label__brand">FERNWHISTLE</div>
    <h1 class="label__name">
      <span class="label__name-line">HARBOUR</span>
      <span class="label__name-line label__name-line--second">MOONS</span>
    </h1>
    <div class="label__type">GIN</div>
    <div class="label__rule"></div>
    <div class="label__specs"><span>42% ALC/VOL</span><span>750ML</span></div>
  </main>
</body>
</html>
```